Business Card Design (NEW FILES)

ATTENTION: New vector files are available. Please update your design to reflect/use the new (better resolution) logo images.

Seeking a unique and professional business card design for a commercial drone photography/videography business. The layout should feature
the logo (attached) and include the following information:
Owen Tarrick
614-502-7738
www.skylarkreelworks.example
NRD Certified Remote Pilot

Owen Tarrick

```html
<!DOCTYPE html>
<html lang="en">
<head>
<meta charset="utf-8">
<title>Skylark Reelworks – Business Card</title>
<link href="https://fonts.googleapis.com/css2?family=Poppins:wght@400;600&display=swap" rel="stylesheet">
<style>
  :root {
    --backdrop: #ababab;
    --navy: #131a47;
    --orange: #ee8a4f;
    --white: #ffffff;
  }
  * { margin: 0; padding: 0; box-sizing: border-box; }
  html, body {
    width: 1093px; height: 1200px; overflow: hidden;
    background: var(--backdrop);
    font-family: 'Poppins', sans-serif;
  }
  .canvas { position: relative; width: 1093px; height: 1200px; }
  .card {
    position: absolute; left: 265px; width: 577px; height: 357px;
    border-radius: 30px; overflow: hidden;
  }
  .card-front { top: 226px; background: var(--white); }
  .card-back { top: 621px; background: var(--navy); }

  .front-brand {
    position: absolute; left: 0; right: 0; top: 82px;
    text-align: center; color: var(--navy);
    font-weight: 600; font-size: 38px; line-height: 46px;
  }
  .front-brand-dot {
    display: block; width: 54px; height: 54px; margin: 0 auto 14px;
    border-radius: 50%; background: var(--orange);
  }
  .identity {
    position: absolute; right: 303px; top: 266px; text-align: right;
  }
  .identity-name {
    color: var(--navy); font-weight: 600; font-size: 28px; line-height: 32px;
    letter-spacing: -0.3px;
  }
  .identity-title {
    color: var(--orange); font-size: 14px; line-height: 18px; letter-spacing: 0.3px;
  }
  .divider {
    position: absolute; left: 288px; top: 273px; width: 1px; height: 38px;
    background: var(--navy);
  }
  .contact {
    position: absolute; left: 303px; top: 270px;
    color: var(--navy); font-size: 16px; line-height: 21px;
  }
  .front-band {
    position: absolute; left: 0; right: 0; bottom: 0; height: 17px;
    background: var(--navy);
  }
  .front-band-notch {
    position: absolute; left: 50%; top: -9px; width: 30px; height: 24px;
    margin-left: -15px; border-radius: 50%; background: var(--white);
  }

  .back-brand {
    position: absolute; left: 0; right: 0; top: 150px;
    display: flex; align-items: center; justify-content: center; gap: 16px;
    color: var(--white); font-weight: 400; font-size: 42px; line-height: 50px;
  }
  .back-brand-dot {
    width: 40px; height: 40px; border-radius: 50%; background: var(--orange);
    flex: none;
  }
  .services {
    position: absolute; left: 0; right: 0; top: 289px; text-align: center;
    font-size: 17.5px; line-height: 21px;
  }
  .services-main { color: var(--white); }
  .services-note { color: var(--orange); }
</style>
</head>
<body>
<main class="canvas">
  <section class="card card-front">
    <div class="front-brand"><span class="front-brand-dot"></span>Skylark Reelworks</div>
    <div class="identity">
      <p class="identity-name">OWEN TARRICK</p>
      <p class="identity-title">NRD CERTIFIED REMOTE PILOT</p>
    </div>
    <div class="divider"></div>
    <div class="contact">
      <p>614-502-7738</p>
      <p>www.skylarkreelworks.example</p>
    </div>
    <div class="front-band"><span class="front-band-notch"></span></div>
  </section>

  <section class="card card-back">
    <div class="back-brand"><span class="back-brand-dot"></span><span>Skylark Reelworks</span></div>
    <div class="services">
      <p class="services-main">Drone Photography and Videography Services</p>
      <p class="services-note">High Quality | Fully Insured</p>
    </div>
  </section>
</main>
</body>
</html>
```